MRT Property - Business Cards

Looking for a business card & general letterhead, signage etc design for our new logo.

Colours:
000a20
0056a2
00b5ef
0088ce
68cef2

Fonts:
Poppins
Karla

Please keep look and feel of new brand - example in the zip package I sent.

```html
<!DOCTYPE html>
<html lang="en">
<head>
<meta charset="utf-8">
<title>MRT Property – Business Card</title>
<link href="https://fonts.googleapis.com/css2?family=Poppins:wght@400;500;600;700&family=Karla:wght@400;600&display=swap" rel="stylesheet">
<style>
  :root{
    --ink:#000a20;
    --brand-blue:#0056a2;
    --band-blue:#1552a3;
    --mid-blue:#0088ce;
    --sky:#00b5ef;
    --pale-sky:#68cef2;
    --paper:#ecebe9;
    --backdrop:#222222;
    --back-top:#0f4d98;
    --back-bottom:#0a3a80;
  }
  *{box-sizing:border-box;margin:0;padding:0}
  html,body{width:1200px;height:780px;overflow:hidden;background:var(--backdrop)}
  body{position:relative;font-family:"Poppins",sans-serif}
  .card{position:absolute;top:240px;width:520px;height:300px;border-radius:20px;overflow:hidden}
  .card--front{left:50px;background:var(--paper)}
  .card--back{left:630px;background:linear-gradient(135deg,var(--back-top),var(--back-bottom))}
  .card__art{position:absolute;inset:0}
  .brand-name{position:absolute;left:34px;top:80px;font-family:"Poppins",sans-serif;font-weight:700;font-size:32px;line-height:1;color:var(--brand-blue);letter-spacing:-.5px;white-space:nowrap}
  .brand-name--small{position:relative;left:auto;top:auto;font-size:15px;color:#ffffff;letter-spacing:0}
  .divider{position:absolute;left:282px;top:44px;width:1px;height:150px;background:var(--brand-blue)}
  .person{position:absolute;left:306px;top:56px}
  .person__name{font-weight:700;font-size:26px;line-height:1.05;color:var(--brand-blue);white-space:nowrap}
  .person__surname{font-weight:400;color:var(--pale-sky)}
  .person__role{font-weight:600;font-size:12px;color:var(--ink);margin-top:2px}
  .contact{list-style:none;margin-top:14px}
  .contact__item{display:flex;align-items:center;gap:8px;font-size:12.5px;color:var(--ink);line-height:21px;white-space:nowrap}
  .contact__icon{width:12px;height:12px;flex:none}
  .address{position:absolute;left:26px;bottom:12px;font-size:11.5px;color:#ffffff;letter-spacing:.2px;white-space:nowrap}
  .pattern{position:absolute;inset:0;background:radial-gradient(ellipse at 85% 70%,rgba(104,206,242,.35),transparent 60%)}
  .back-mark{position:absolute;left:0;right:0;bottom:54px;display:flex;justify-content:center}
</style>
</head>
<body>

<section class="card card--front">
  <svg class="card__art" viewBox="0 0 520 300" aria-hidden="true">
    <path d="M0 150 C120 162 175 225 300 246 S470 258 520 280 L520 300 L0 300 Z" fill="var(--band-blue)"/>
    <path d="M0 158 C120 170 175 233 300 254 S470 266 520 288" fill="none" stroke="var(--pale-sky)" stroke-width="4"/>
  </svg>

  <div class="brand-name">MRT Property</div>
  <div class="divider"></div>

  <div class="person">
    <div class="person__name">Lachlan <span class="person__surname">Reid</span></div>
    <div class="person__role">Director</div>
    <ul class="contact">
      <li class="contact__item">
        <svg class="contact__icon" viewBox="0 0 12 12"><path d="M2.5 1 L4.5 1 L5 3.5 L3.8 4.5 C4.5 6 6 7.5 7.5 8.2 L8.5 7 L11 7.5 L11 9.5 C11 10.4 10.3 11 9.5 11 C5 11 1 7 1 2.5 C1 1.7 1.6 1 2.5 1Z" fill="var(--mid-blue)"/></svg>
        +61 2 9000 1234
      </li>
      <li class="contact__item">
        <svg class="contact__icon" viewBox="0 0 12 12"><circle cx="6" cy="6" r="5" fill="none" stroke="var(--mid-blue)" stroke-width="1.2"/><ellipse cx="6" cy="6" rx="2" ry="5" fill="none" stroke="var(--mid-blue)" stroke-width="1"/><line x1="1" y1="6" x2="11" y2="6" stroke="var(--mid-blue)" stroke-width="1"/></svg>
        www.mrtproperty.com.au
      </li>
      <li class="contact__item">
        <svg class="contact__icon" viewBox="0 0 12 12"><rect x="1" y="2.5" width="10" height="7" rx="1" fill="var(--mid-blue)"/><path d="M1.5 3 L6 6.5 L10.5 3" fill="none" stroke="#ffffff" stroke-width="1"/></svg>
        info@mrtproperty.com.au
      </li>
    </ul>
  </div>

  <p class="address">Suite 4.12, Level 4, 18 Harbour Lane, Riverside NSW 2199</p>
</section>

<section class="card card--back">
  <div class="pattern" role="img" aria-label="Repeating brand pattern in deep and light blue tones"></div>
  <div class="back-mark"><span class="brand-name brand-name--small">MRT Property</span></div>
</section>

</body>
</html>
```